Dental Medical History Form - Content provided

Design a medical history form for a dental practice. Content is provided so all that is needed is the formatting to make it look great and easy to read.

"Patient Information" to include all information contained in top portion of the "Patient Medical History Form" docx file.

"Medical History" should follow the formatting and content of the "Exact Medical History" file as this is what the entry fields look like in our practice software and so we would like it to match.

1st page - Patient info, allergies, medications, antibiotics, joint replacement, pregnancy.

2nd page - Do you have, or have you had, any of the following? . . . . . . .
Updates

Target Market(s)

All ages but must be clear enough for elderly to read. Use as much space as possible to keep font size bigger yet keep to two pages

Industry/Entity Type

Dental

Font styles to use
Sans Serif

Requirements
Must have
• All content provided
• Our logo at the top (file provided)
• Century Gothic Font
• Limit to two pages

```html
<!DOCTYPE html>
<html lang="en">
<head>
<meta charset="utf-8">
<title>Medical History – Page 2</title>
<link rel="stylesheet" href="https://fonts.googleapis.com/css2?family=PT+Sans+Narrow:wght@400;700&display=swap">
<style>
  :root{
    --backdrop:#e4e4e6;
    --paper:#ffffff;
    --ink:#2b3650;
    --rule:#3a4560;
    --band-dark:#8d8f99;
    --band-light:#f1f1f3;
    --box:#3a4560;
  }
  *{box-sizing:border-box;margin:0;padding:0}
  html,body{width:1200px;height:784px;overflow:hidden}
  body{background:var(--backdrop);font-family:"PT Sans Narrow",Arial Narrow,sans-serif;color:var(--ink)}
  .sheet{position:absolute;left:320px;top:20px;width:560px;height:744px;background:var(--paper);box-shadow:0 2px 8px rgba(0,0,0,.12)}
  .band{position:absolute;left:0;right:0;height:30px;background:linear-gradient(var(--band-dark),var(--band-light))}
  .band--top{top:0;border-bottom:2px solid var(--rule)}
  .band--bottom{bottom:0;height:18px;background:linear-gradient(var(--band-light),var(--band-dark))}
  .sheet-title{position:absolute;top:5px;right:24px;font-size:15px;font-weight:700;color:var(--ink)}
  .checklist{position:absolute;top:48px;left:26px;right:20px;display:grid;grid-template-columns:1fr 1fr;column-gap:22px}
  .row{display:flex;align-items:center;height:14px;font-size:10.5px;line-height:14px}
  .row .label{flex:0 0 168px;white-space:nowrap;overflow:hidden}
  .row.heading .label{font-weight:700;font-size:11px}
  .answer{display:flex;align-items:center;gap:3px;font-size:9.5px}
  .answer + .answer{margin-left:6px}
  .tick-box{width:9px;height:9px;border:1px solid var(--box);display:inline-block}
  .col-right{padding-top:14px}
  .closing{position:absolute;left:26px;right:26px;top:620px;font-size:10px;line-height:13px}
  .sign-off{position:absolute;left:26px;right:26px;top:680px;display:flex;gap:40px}
  .field{flex:1;display:flex;align-items:flex-end;gap:8px;font-size:12px;font-weight:700}
  .field .line{flex:1;border-bottom:1px solid var(--rule);height:14px}
  .field--date{flex:0 0 170px}
</style>
</head>
<body>
<main class="sheet">
  <div class="band band--top"></div>
  <h1 class="sheet-title">Do you have, or have you had, any of the following?</h1>

  <section class="checklist">
    <div class="col-left">
      <div class="row heading"><span class="label">Dental</span></div>
      <div class="row"><span class="label">Acid Reflux</span><span class="answer">Yes <i class="tick-box"></i></span><span class="answer">No <i class="tick-box"></i></span></div>
      <div class="row"><span class="label">Bad Breath/Taste</span><span class="answer">Yes <i class="tick-box"></i></span><span class="answer">No <i class="tick-box"></i></span></div>
      <div class="row"><span class="label">Bleeding/Swollen/Sore Gums</span><span class="answer">Yes <i class="tick-box"></i></span><span class="answer">No <i class="tick-box"></i></span></div>
      <div class="row"><span class="label">Blisters/Ulcers in Mouth</span><span class="answer">Yes <i class="tick-box"></i></span><span class="answer">No <i class="tick-box"></i></span></div>
      <div class="row"><span class="label">Broken tooth/filling</span><span class="answer">Yes <i class="tick-box"></i></span><span class="answer">No <i class="tick-box"></i></span></div>
      <div class="row"><span class="label">Burning tongue</span><span class="answer">Yes <i class="tick-box"></i></span><span class="answer">No <i class="tick-box"></i></span></div>
      <div class="row"><span class="label">Dry mouth</span><span class="answer">Yes <i class="tick-box"></i></span><span class="answer">No <i class="tick-box"></i></span></div>
      <div class="row"><span class="label">Food collection between teeth</span><span class="answer">Yes <i class="tick-box"></i></span><span class="answer">No <i class="tick-box"></i></span></div>
      <div class="row"><span class="label">Grinding/clenching teeth (day/night)</span><span class="answer">Yes <i class="tick-box"></i></span><span class="answer">No <i class="tick-box"></i></span></div>
      <div class="row"><span class="label">Loose teeth</span><span class="answer">Yes <i class="tick-box"></i></span><span class="answer">No <i class="tick-box"></i></span></div>
      <div class="row"><span class="label">Crooked teeth</span><span class="answer">Yes <i class="tick-box"></i></span><span class="answer">No <i class="tick-box"></i></span></div>
      <div class="row"><span class="label">Discoloured teeth</span><span class="answer">Yes <i class="tick-box"></i></span><span class="answer">No <i class="tick-box"></i></span></div>
      <div class="row"><span class="label">Sensitivity to Hot/Cold</span><span class="answer">Yes <i class="tick-box"></i></span><span class="answer">No <i class="tick-box"></i></span></div>
      <div class="row"><span class="label">Tooth pain when chewing</span><span class="answer">Yes <i class="tick-box"></i></span><span class="answer">No <i class="tick-box"></i></span></div>
      <div class="row"><span class="label">Jaw pain/Fracture</span><span class="answer">Yes <i class="tick-box"></i></span><span class="answer">No <i class="tick-box"></i></span></div>
      <div class="row"><span class="label">Orthodontic treatment/history</span><span class="answer">Yes <i class="tick-box"></i></span><span class="answer">No <i class="tick-box"></i></span></div>
      <div class="row"><span class="label">Oral Cancer</span><span class="answer">Yes <i class="tick-box"></i></span><span class="answer">No <i class="tick-box"></i></span></div>
      <div class="row heading"><span class="label">Diet/Lifestyle</span></div>
      <div class="row"><span class="label">Drink more than one glass alcohol per day</span><span class="answer">Yes <i class="tick-box"></i></span><span class="answer">No <i class="tick-box"></i></span></div>
      <div class="row"><span class="label">Smoking</span><span class="answer">Yes <i class="tick-box"></i></span><span class="answer">No <i class="tick-box"></i></span></div>
      <div class="row"><span class="label">Carbonated drinks</span><span class="answer">Yes <i class="tick-box"></i></span><span class="answer">No <i class="tick-box"></i></span></div>
      <div class="row"><span class="label">Sugary foods</span><span class="answer">Yes <i class="tick-box"></i></span><span class="answer">No <i class="tick-box"></i></span></div>
      <div class="row heading"><span class="label">Blood</span></div>
      <div class="row"><span class="label">Anaemia</span><span class="answer">Yes <i class="tick-box"></i></span><span class="answer">No <i class="tick-box"></i></span></div>
      <div class="row"><span class="label">Blood Clots</span><span class="answer">Yes <i class="tick-box"></i></span><span class="answer">No <i class="tick-box"></i></span></div>
      <div class="row"><span class="label">Leukemia</span><span class="answer">Yes <i class="tick-box"></i></span><span class="answer">No <i class="tick-box"></i></span></div>
      <div class="row"><span class="label">Low platelets</span><span class="answer">Yes <i class="tick-box"></i></span><span class="answer">No <i class="tick-box"></i></span></div>
      <div class="row"><span class="label">Lymphoma</span><span class="answer">Yes <i class="tick-box"></i></span><span class="answer">No <i class="tick-box"></i></span></div>
      <div class="row"><span class="label">Haemophilia</span><span class="answer">Yes <i class="tick-box"></i></span><span class="answer">No <i class="tick-box"></i></span></div>
      <div class="row heading"><span class="label">Chest</span></div>
      <div class="row"><span class="label">Bronchitis</span><span class="answer">Yes <i class="tick-box"></i></span><span class="answer">No <i class="tick-box"></i></span></div>
      <div class="row"><span class="label">Cystic Fibrosis</span><span class="answer">Yes <i class="tick-box"></i></span><span class="answer">No <i class="tick-box"></i></span></div>
      <div class="row"><span class="label">Emphysema</span><span class="answer">Yes <i class="tick-box"></i></span><span class="answer">No <i class="tick-box"></i></span></div>
      <div class="row"><span class="label">Pneumonia</span><span class="answer">Yes <i class="tick-box"></i></span><span class="answer">No <i class="tick-box"></i></span></div>
      <div class="row heading"><span class="label">Infectious Disease</span></div>
      <div class="row"><span class="label">Creutzfeldt-Jakob Disease</span><span class="answer">Yes <i class="tick-box"></i></span><span class="answer">No <i class="tick-box"></i></span></div>
      <div class="row"><span class="label">Hepatitis A,B,C,D</span><span class="answer">Yes <i class="tick-box"></i></span><span class="answer">No <i class="tick-box"></i></span></div>
    </div>

    <div class="col-right">
      <div class="row"><span class="label">HIV/AIDS</span><span class="answer">Yes <i class="tick-box"></i></span><span class="answer">No <i class="tick-box"></i></span></div>
      <div class="row"><span class="label">Influenza</span><span class="answer">Yes <i class="tick-box"></i></span><span class="answer">No <i class="tick-box"></i></span></div>
      <div class="row"><span class="label">Shingles</span><span class="answer">Yes <i class="tick-box"></i></span><span class="answer">No <i class="tick-box"></i></span></div>
      <div class="row"><span class="label">Tuberculosis</span><span class="answer">Yes <i class="tick-box"></i></span><span class="answer">No <i class="tick-box"></i></span></div>
      <div class="row heading"><span class="label">Heart</span></div>
      <div class="row"><span class="label">Angina</span><span class="answer">Yes <i class="tick-box"></i></span><span class="answer">No <i class="tick-box"></i></span></div>
      <div class="row"><span class="label">Atrial Fibrillation</span><span class="answer">Yes <i class="tick-box"></i></span><span class="answer">No <i class="tick-box"></i></span></div>
      <div class="row"><span class="label">Blood Pressure (High/Low)</span><span class="answer">Yes <i class="tick-box"></i></span><span class="answer">No <i class="tick-box"></i></span></div>
      <div class="row"><span class="label">Congenital Heart Disease</span><span class="answer">Yes <i class="tick-box"></i></span><span class="answer">No <i class="tick-box"></i></span></div>
      <div class="row"><span class="label">Heart attack</span><span class="answer">Yes <i class="tick-box"></i></span><span class="answer">No <i class="tick-box"></i></span></div>
      <div class="row"><span class="label">Heart murmur</span><span class="answer">Yes <i class="tick-box"></i></span><span class="answer">No <i class="tick-box"></i></span></div>
      <div class="row"><span class="label">Heart surgery</span><span class="answer">Yes <i class="tick-box"></i></span><span class="answer">No <i class="tick-box"></i></span></div>
      <div class="row"><span class="label">Heart valve replacement</span><span class="answer">Yes <i class="tick-box"></i></span><span class="answer">No <i class="tick-box"></i></span></div>
      <div class="row"><span class="label">Infective endocarditis</span><span class="answer">Yes <i class="tick-box"></i></span><span class="answer">No <i class="tick-box"></i></span></div>
      <div class="row"><span class="label">Rheumatic Heart Disease</span><span class="answer">Yes <i class="tick-box"></i></span><span class="answer">No <i class="tick-box"></i></span></div>
      <div class="row"><span class="label">Pacemaker</span><span class="answer">Yes <i class="tick-box"></i></span><span class="answer">No <i class="tick-box"></i></span></div>
      <div class="row"><span class="label">Stent</span><span class="answer">Yes <i class="tick-box"></i></span><span class="answer">No <i class="tick-box"></i></span></div>
      <div class="row heading"><span class="label">Other</span></div>
      <div class="row"><span class="label">Anxiety/PTSD</span><span class="answer">Yes <i class="tick-box"></i></span><span class="answer">No <i class="tick-box"></i></span></div>
      <div class="row"><span class="label">Arthritis</span><span class="answer">Yes <i class="tick-box"></i></span><span class="answer">No <i class="tick-box"></i></span></div>
      <div class="row"><span class="label">Alzheimer's</span><span class="answer">Yes <i class="tick-box"></i></span><span class="answer">No <i class="tick-box"></i></span></div>
      <div class="row"><span class="label">Asthma</span><span class="answer">Yes <i class="tick-box"></i></span><span class="answer">No <i class="tick-box"></i></span></div>
      <div class="row"><span class="label">Anaphylaxis</span><span class="answer">Yes <i class="tick-box"></i></span><span class="answer">No <i class="tick-box"></i></span></div>
      <div class="row"><span class="label">Auto-immune disease</span><span class="answer">Yes <i class="tick-box"></i></span><span class="answer">No <i class="tick-box"></i></span></div>
      <div class="row"><span class="label">Coeliac</span><span class="answer">Yes <i class="tick-box"></i></span><span class="answer">No <i class="tick-box"></i></span></div>
      <div class="row"><span class="label">Depression</span><span class="answer">Yes <i class="tick-box"></i></span><span class="answer">No <i class="tick-box"></i></span></div>
      <div class="row"><span class="label">Diabetes</span><span class="answer">Yes <i class="tick-box"></i></span><span class="answer">No <i class="tick-box"></i></span></div>
      <div class="row"><span class="label">Epilepsy</span><span class="answer">Yes <i class="tick-box"></i></span><span class="answer">No <i class="tick-box"></i></span></div>
      <div class="row"><span class="label">Kidney Disease</span><span class="answer">Yes <i class="tick-box"></i></span><span class="answer">No <i class="tick-box"></i></span></div>
      <div class="row"><span class="label">Liver Disease</span><span class="answer">Yes <i class="tick-box"></i></span><span class="answer">No <i class="tick-box"></i></span></div>
      <div class="row"><span class="label">Osteoporosis</span><span class="answer">Yes <i class="tick-box"></i></span><span class="answer">No <i class="tick-box"></i></span></div>
      <div class="row"><span class="label">Parkinson's</span><span class="answer">Yes <i class="tick-box"></i></span><span class="answer">No <i class="tick-box"></i></span></div>
      <div class="row"><span class="label">Radiation to Head/Neck</span><span class="answer">Yes <i class="tick-box"></i></span><span class="answer">No <i class="tick-box"></i></span></div>
      <div class="row"><span class="label">Schizophrenia</span><span class="answer">Yes <i class="tick-box"></i></span><span class="answer">No <i class="tick-box"></i></span></div>
      <div class="row"><span class="label">Snoring</span><span class="answer">Yes <i class="tick-box"></i></span><span class="answer">No <i class="tick-box"></i></span></div>
      <div class="row"><span class="label">Sleep apnea</span><span class="answer">Yes <i class="tick-box"></i></span><span class="answer">No <i class="tick-box"></i></span></div>
      <div class="row"><span class="label">Stroke</span><span class="answer">Yes <i class="tick-box"></i></span><span class="answer">No <i class="tick-box"></i></span></div>
    </div>
  </section>

  <p class="closing">Thank you for the time to complete your medical history form.<br>
  Oral health is linked to overall health and this comprehensive questionnaire will help us to provide you with optimal and safe care.</p>

  <div class="sign-off">
    <div class="field field--date">Date <span class="line"></span></div>
    <div class="field">Signature <span class="line"></span></div>
  </div>

  <div class="band band--bottom"></div>
</main>
</body>
</html>
```